TPW other templates

1) Internal pages for the documents that we write. basically what will the pages inside look like. It should basically be a document with a header, a footer and a page number locator. It should include the following information: name of the report, date, TPW logo somehow, and version (draft, final etc). the information should be divided between header and footer. let me know if its unclear. As with everything it should work both in black and white and in color in case it is printed in black and white :-)
2) chapter dividers. This are the pages that you might have inside the report to separate sections. It should just have a page number, and chapter or section name. Simple, but again follow the same idea of the design that you created. It should be possible to have a picture in the divider, but it should not be a must. so in that sense we need to versions.
3) Business cards. Should include space for name, title, phone numbers (2 or 3), email, Skype, web page, and the company address which you have already.
4) a signature for emails. Basically the file that is glued to the bottom off all emails as a signature. Again it should include all the information in the business cards.

Not including any files since you have already designed others

```html
<!DOCTYPE html>
<html lang="en">
<head>
<meta charset="utf-8">
<title>TPW – Chapter Divider</title>
<link href="https://fonts.googleapis.com/css2?family=Raleway:wght@200;300;400&display=swap" rel="stylesheet">
<style>
  :root {
    --backdrop: #e4e7ea;
    --paper: #ffffff;
    --ink-dark: #6f6f72;
    --ink-mid: #8c8c8f;
    --ink-light: #b4b4b6;
    --band-1: #ededee;
    --band-2: #e2e2e4;
    --band-3: #d7d7d9;
  }
  * { margin: 0; padding: 0; box-sizing: border-box; }
  html, body {
    width: 1200px;
    height: 1000px;
    overflow: hidden;
    background: var(--backdrop);
    font-family: "Raleway", sans-serif;
  }
  .divider-page {
    position: absolute;
    left: 289px;
    top: 60px;
    width: 622px;
    height: 880px;
    background: var(--paper);
    box-shadow: 0 2px 10px rgba(0,0,0,0.08);
    overflow: hidden;
  }
  .side-bands {
    position: absolute;
    left: 0;
    top: 0;
    width: 622px;
    height: 880px;
  }
  .brand {
    position: absolute;
    top: 34px;
    right: 40px;
    text-align: center;
    color: var(--ink-dark);
  }
  .brand-name {
    font-size: 30px;
    font-weight: 400;
    letter-spacing: 1px;
    line-height: 1;
  }
  .brand-version {
    font-size: 9px;
    font-weight: 300;
    letter-spacing: 1px;
    color: var(--ink-mid);
    margin-top: 2px;
  }
  .chapter-title {
    position: absolute;
    left: 150px;
    top: 520px;
    text-transform: uppercase;
    font-weight: 200;
    line-height: 1.05;
  }
  .chapter-number {
    font-size: 40px;
    color: var(--ink-dark);
    font-weight: 300;
  }
  .chapter-name {
    font-size: 27px;
    color: var(--ink-light);
    letter-spacing: 0.5px;
  }
  .page-number {
    position: absolute;
    right: 40px;
    top: 612px;
    font-size: 14px;
    font-weight: 300;
    color: var(--ink-mid);
    letter-spacing: 2px;
  }
</style>
</head>
<body>
  <main class="divider-page">
    <svg class="side-bands" viewBox="0 0 622 880" aria-hidden="true">
      <path d="M0 0 C 60 120, 120 260, 150 420 C 175 560, 170 720, 160 880 L 0 880 Z" fill="var(--band-1)"/>
      <path d="M0 40 C 70 170, 110 320, 125 470 C 140 620, 140 760, 130 880 L 0 880 Z" fill="var(--band-2)" opacity="0.8"/>
      <path d="M0 150 C 50 260, 85 400, 95 540 C 105 680, 100 800, 90 880 L 0 880 Z" fill="var(--band-3)" opacity="0.6"/>
      <path d="M0 300 C 30 420, 55 560, 60 700 C 62 790, 58 850, 55 880 L 0 880 Z" fill="var(--band-2)" opacity="0.7"/>
    </svg>

    <header class="brand">
      <div class="brand-name">TPW</div>
      <div class="brand-version">-Draft-</div>
    </header>

    <h1 class="chapter-title">
      <span class="chapter-number">Part III:</span><br>
      <span class="chapter-name">Conclusions<br>&amp; Recommendations</span>
    </h1>

    <div class="page-number">- 79 -</div>
  </main>
</body>
</html>
```